Brightfield Ventures Inc. Letterhead

Creation of attractive and eye catching letterhead for a business start-up for the construction industry. Letterhead must relate to construction, but avoid standard hammer and tools in the design.

I forgot to add some details, sorry about that. Some pertinent info: Ph: 916-555-0187 brightfieldventures.example 448 Willowmere Ave, Ste 210 Folsom, CA 95999 info@brightfieldventures.example not sure if slogan should be in there" “Connecting construction professionals to create a purpose driven industry.” must be able to be used in word. Thanks!

```html
<!DOCTYPE html>
<html lang="en">
<head>
<meta charset="utf-8">
<title>Brightfield Ventures Inc. Letterhead</title>
<link rel="stylesheet" href="https://fonts.googleapis.com/css2?family=Open+Sans:wght@400;600;700&family=Montserrat:wght@600&display=swap">
<style>
  :root {
    --navy: #0f1c57;
    --red: #c0111d;
    --ink: #2a2a2a;
    --paper: #ffffff;
    --backdrop: #e9eaec;
  }
  * { box-sizing: border-box; margin: 0; padding: 0; }
  html, body { width: 1200px; height: 784px; overflow: hidden; }
  body {
    background: var(--backdrop);
    font-family: "Open Sans", Arial, sans-serif;
    color: var(--ink);
    position: relative;
  }
  .letterhead {
    position: absolute;
    left: 314px; top: 22px;
    width: 572px; height: 740px;
    background: var(--paper);
    overflow: hidden;
    box-shadow: 0 4px 18px rgba(0,0,0,0.12);
  }
  .brand {
    position: absolute; left: 52px; top: 48px;
    display: flex; align-items: center; gap: 8px;
  }
  .brand-mark { width: 14px; height: 14px; background: var(--red); }
  .brand-name {
    font-family: "Montserrat", Arial, sans-serif;
    font-weight: 600; font-size: 13px; letter-spacing: 1.5px;
    color: var(--navy); text-transform: uppercase;
  }
  .brand-rule {
    position: absolute; left: 52px; top: 72px;
    width: 150px; height: 1.5px; background: var(--red);
  }
  .letter-body {
    position: absolute; left: 60px; top: 128px; width: 440px;
  }
  .salutation { font-weight: 700; font-size: 12px; color: #111; margin-bottom: 12px; }
  .letter-body p {
    font-size: 10px; line-height: 1.5; margin-bottom: 14px;
  }
  .signature {
    width: 110px; height: 44px; margin-top: 14px; margin-left: 120px;
    background: linear-gradient(90deg, rgba(0,0,0,0.04), rgba(0,0,0,0.10), rgba(0,0,0,0.04));
    border-radius: 4px;
  }
  .footer-wave { position: absolute; left: 0; bottom: 0; width: 572px; height: 150px; }
  .contact {
    position: absolute; right: 22px; bottom: 14px;
    text-align: right; color: #fff; font-size: 7.5px; line-height: 1.7;
  }
  .contact li { list-style: none; display: flex; justify-content: flex-end; align-items: center; gap: 5px; }
  .contact svg { width: 7px; height: 7px; fill: #fff; }
</style>
</head>
<body>
  <main class="letterhead">
    <div class="brand">
      <span class="brand-mark"></span>
      <span class="brand-name">Brightfield Ventures</span>
    </div>
    <div class="brand-rule"></div>

    <section class="letter-body">
      <p class="salutation">Dear Mr. Harlow,</p>
      <p>Lorem Ipsum is simply dummy text of the printing and typesetting industry. Lorem Ipsum has been the industry's standard dummy text ever since the 1500s, when an unknown printer took a galley of type and scrambled it to make a type specimen book. It has survived not only five centuries, but also the leap into electronic typesetting, remaining essentially unchanged.</p>
      <p>The standard chunk of Lorem Ipsum used since the 1500s is reproduced below for those interested. Sections 1.10.32 and 1.10.33 from "de Finibus Bonorum et Malorum" by Cicero are also reproduced in their exact original form, accompanied by English versions from the 1914 translation by H. Rackham.</p>
      <p>Lorem Ipsum is simply dummy text of the printing and typesetting industry. Lorem Ipsum has been the industry's standard dummy text ever since the 1500s, when an unknown printer took a galley of type and scrambled it to make a type specimen book. It has survived not only five centuries, but also the leap into electronic typesetting, remaining essentially unchanged. It was popularised in the</p>
      <p>The standard chunk of Lorem Ipsum used since the 1500s is reproduced below for those interested. Sections 1.10.32 and 1.10.33 from "de Finibus Bonorum et Malorum" by Cicero are also reproduced in their exact original form, accompanied by English versions from the 1914 translation by H. Rackham.</p>
      <div class="signature" role="img" aria-label="Handwritten signature of the sender"></div>
    </section>

    <svg class="footer-wave" viewBox="0 0 572 150" preserveAspectRatio="none" aria-hidden="true">
      <path d="M0,150 L0,138 C220,132 430,90 572,4 L572,150 Z" fill="var(--navy)"/>
      <path d="M0,136 C220,128 420,86 560,0 L572,0 C430,92 220,134 0,140 Z" fill="var(--red)"/>
      <path d="M0,128 C210,120 410,78 540,0 L548,0 C418,82 214,124 0,131 Z" fill="var(--red)"/>
    </svg>

    <ul class="contact">
      <li>Ph: 916-555-0187 <svg viewBox="0 0 10 10"><path d="M2 0h2l1 3-1.5 1a6 6 0 0 0 2.5 2.5L7 5l3 1v2a2 2 0 0 1-2 2A8 8 0 0 1 0 2a2 2 0 0 1 2-2z"/></svg></li>
      <li>info@brightfieldventures.example <svg viewBox="0 0 10 10"><path d="M0 2h10v6H0z M0 2l5 3.5L10 2" stroke="#0f1c57" stroke-width="0.8"/></svg></li>
      <li>brightfieldventures.example <svg viewBox="0 0 10 10"><circle cx="5" cy="5" r="4.5"/></svg></li>
      <li>448 Willowmere Ave, Ste 210, Folsom, CA 95999 <svg viewBox="0 0 10 10"><path d="M5 0a3.5 3.5 0 0 1 3.5 3.5C8.5 6 5 10 5 10S1.5 6 1.5 3.5A3.5 3.5 0 0 1 5 0z"/></svg></li>
    </ul>
  </main>
</body>
</html>
```